Diabetes control iOS/Android app design

I need a modern app design with light colors that are easy on the eyes, This app is for diabetes control. Focusing on Sweet/carb control and its daily intake .. I have uploaded some wireframe pages to design . Light colors are preferred for design. I donot need too much Hussle and data on main page.
Name/title: Glimwell- Diabetes reversal

Target Market(s)

Diabetes patients

Industry/Entity Type

health

Colors
0094D4
00A9DD
6FCCEA
C7EBF8
E9F6FB
00AB8E
00BBA5
67D7C9
C6EFE9
E9F9F6
59FF00
82FF00
B8FF75
E3FFCB
F4FFEA
FFC000
F8CF3A
FAE287
FDF2CF
FEFAEE

Requirements
Should not have
• complicated design. It should be simple , modern and easy o eye.

```html
<!DOCTYPE html>
<html lang="en">
<head>
<meta charset="utf-8">
<title>Glimwell – Diabetes Reversal app screens</title>
<link href="https://fonts.googleapis.com/css2?family=Nunito:ital,wght@0,400;0,600;0,700;0,800;0,900;1,400&display=swap" rel="stylesheet">
<style>
:root{
  --stage:#4a4849;
  --card:#ffffff;
  --blue:#0094D4;
  --blue-bright:#00A9DD;
  --blue-pale:#C7EBF8;
  --yellow:#FFC000;
  --yellow-soft:#F8CF3A;
  --teal:#00AB8E;
  --teal-pale:#C6EFE9;
  --red:#e8202a;
  --red-pale:#f7cdd0;
  --ink:#1c1c1c;
  --grey:#555555;
  --muted:#8a8a8a;
  --rule:#d6eaf2;
  --nav-btn:#4fa3a6;
  --pink:#ef6f8e;
  --violet:#7b7fe0;
}
*{box-sizing:border-box;margin:0;padding:0}
html,body{width:1200px;height:649px;overflow:hidden;background:var(--stage);font-family:"Nunito",sans-serif}
.stage{position:relative;width:1200px;height:649px}
.screen{position:absolute;top:43px;width:260px;height:562px;background:var(--card);border-radius:19px}
.screen--feed-summary{left:45px}
.screen--monitor{left:328px}
.screen--daily-feed{left:612px}
.screen--plan{left:895px}

/* header */
.brand{position:absolute;left:37px;top:20px;display:flex;align-items:center;gap:11px}
.brand__dot{width:24px;height:24px;border-radius:50%;background:var(--blue)}
.brand__name{color:var(--ink);font-weight:800;line-height:1}
.brand__title{font-size:16px;letter-spacing:.3px}
.brand__tagline{font-size:10.5px;letter-spacing:3px;margin-top:5px}
.header-rule{position:absolute;left:21px;right:20px;top:66px;height:1px;background:#ece6d2}

/* section bar */
.section-bar{position:absolute;left:22px;top:80px;width:218px;height:39px;background:var(--yellow);border-radius:8px;display:flex;align-items:center}
.section-bar__icon{width:34px;height:35px;margin-left:3px;border-radius:7px;background:var(--blue);display:flex;align-items:center;justify-content:center}
.section-bar__label{margin-left:20px;color:var(--blue);font-weight:800;font-size:13px;letter-spacing:.3px}

/* sugar count */
.sugar-card{position:absolute;left:10px;top:78px;width:241px;height:154px;border-radius:12px;overflow:hidden;background:var(--blue)}
.sugar-card__photo{position:absolute;right:0;top:0;width:120px;height:154px;background:linear-gradient(135deg,#dfe9ef,#9cc4df 45%,#3a78b9 70%,#e8eef2);clip-path:polygon(25% 0,100% 0,100% 100%,0 100%)}
.sugar-card__icon{position:absolute;left:21px;top:20px}
.sugar-card__title{position:absolute;left:21px;top:43px;color:#fff;font-weight:900;font-size:14.5px}
.sugar-card__today{position:absolute;left:21px;top:103px;color:#fff;font-size:11px}
.sugar-card__goal{position:absolute;left:21px;top:123px;color:var(--yellow);font-size:11px;display:flex;align-items:center;gap:8px}

.consumption-title{position:absolute;left:13px;top:253px;display:flex;align-items:center;gap:10px;font-weight:900;font-size:14px;color:var(--ink)}
.consumption-title__dot{width:16px;height:16px;border-radius:50%;background:var(--blue)}
.meter{position:absolute;left:11px;width:238px}
.meter__track{position:relative;height:2px}
.meter__fill{position:absolute;left:0;top:0;height:2px}
.meter__knob{position:absolute;top:-2px;width:5px;height:5px;border-radius:50%}
.meter__scale{position:relative;height:12px;margin-top:10px;font-size:7.5px}
.meter__scale span{position:absolute;top:0;transform:translateX(-50%);color:var(--grey)}
.meter__scale .meter__name{left:0;transform:none}
.meter--danger{top:288px}
.meter--danger .meter__track{background:var(--red-pale)}
.meter--danger .meter__fill,.meter--danger .meter__knob{background:var(--red)}
.meter--danger .meter__name{color:var(--red)}
.meter--fatal{top:335px}
.meter--fatal .meter__track{background:var(--teal-pale)}
.meter--fatal .meter__fill,.meter--fatal .meter__knob{background:var(--teal)}
.meter--fatal .meter__name{color:var(--teal)}
.meter--catastrophe{top:381px}
.meter--catastrophe .meter__track{background:var(--blue-pale)}
.meter--catastrophe .meter__fill,.meter--catastrophe .meter__knob{background:var(--blue)}
.meter--catastrophe .meter__name{color:var(--blue)}

/* charts */
.chart-card{position:absolute;left:22px;width:216px;background:#fff;border-radius:12px;box-shadow:0 2px 10px rgba(0,0,0,.08)}
.chart-card--bars{top:136px;height:139px}
.chart-card--lines{top:312px;height:131px}
.legend{position:absolute;display:flex;gap:14px;align-items:center;color:var(--grey)}
.legend span{display:flex;align-items:center;gap:6px}
.legend i{display:block;border-radius:2px}
.legend--bars{left:0;right:0;top:285px;justify-content:center;font-size:10px;gap:20px}
.legend--bars i{width:10px;height:10px}
.legend--lines{left:0;right:0;top:107px;justify-content:center;font-size:7px}
.legend--lines i{width:7px;height:7px}
.swatch-blue{background:var(--blue)}
.swatch-yellow{background:var(--yellow)}
.stats{position:absolute;top:458px;left:0;right:0;height:34px}
.stat{position:absolute;top:0;text-align:center;transform:translateX(-50%)}
.stat--weekly{left:88px}
.stat--avg{left:195px}
.stat__value{color:var(--blue);font-weight:800;font-size:16px;line-height:1}
.stat__label{color:var(--grey);font-size:8px;margin-top:6px;white-space:nowrap}
.stats__divider{position:absolute;left:153px;top:0;width:1px;height:33px;background:#e3e3e3}

/* form */
.field{position:absolute;left:26px;width:208px;border-bottom:1px solid var(--rule);padding-bottom:9px}
.field__label{color:var(--blue);font-weight:700;font-size:9.5px}
.field__input{color:var(--grey);font-style:italic;font-size:7px;margin-top:8px}
.field--fasting{top:139px}
.field--random{top:193px}
.field--walk{top:248px}

/* plan */
.plan-intro{position:absolute;left:26px;top:139px;width:222px;color:var(--ink);font-weight:700;font-size:9.5px;line-height:1.4}
.plan-lead{position:absolute;left:26px;top:175px;color:var(--blue);font-weight:800;font-size:9.5px}
.step{position:absolute;left:27px;width:65px;height:23px;background:var(--yellow);border-radius:0 12px 12px 0;color:var(--blue);font-weight:800;font-size:9.5px;display:flex;align-items:center;padding-left:14px}
.step--1{top:199px}.step--2{top:259px}.step--3{top:319px}
.step-text{position:absolute;left:41px;color:var(--grey);font-size:9.5px}
.step-text--1{top:231px}.step-text--2{top:291px}.step-text--3{top:351px}

/* nav */
.tab-bar{position:absolute;left:12px;top:506px;width:237px;height:46px;background:var(--blue);border-radius:8px;display:flex;align-items:center;justify-content:center;gap:7px}
.tab-bar__btn{width:30px;height:30px;border-radius:5px;background:var(--nav-btn);display:flex;align-items:center;justify-content:center}
.tab-bar__start{width:66px;height:30px;border-radius:5px;background:var(--yellow);display:flex;align-items:center;justify-content:center;gap:6px;color:#fff;font-size:12.5px;font-weight:600}
</style>
</head>
<body>
<div class="stage">

<!-- Screen 1 : sugar count -->
<section class="screen screen--feed-summary">
  <header class="brand"><span class="brand__dot"></span><div class="brand__name"><div class="brand__title">GLIMWELL</div><div class="brand__tagline">DIABETES REVERSAL</div></div></header>
  <div class="header-rule"></div>
  <div class="sugar-card">
    <div class="sugar-card__photo" role="img" aria-label="Gloved hands testing blood sugar with a glucose meter"></div>
    <svg class="sugar-card__icon" width="20" height="18" viewBox="0 0 20 18"><rect x="1" y="4" width="10" height="12" rx="2" fill="none" stroke="#FFC000" stroke-width="2"/><rect x="4" y="1" width="4" height="3" fill="#FFC000"/><rect x="3.5" y="7" width="5" height="3" fill="#FFC000"/><circle cx="15" cy="13" r="4" fill="#FFC000"/></svg>
    <div class="sugar-card__title">SUGAR COUNT</div>
    <div class="sugar-card__today">1 sugar today</div>
    <div class="sugar-card__goal"><svg width="10" height="10" viewBox="0 0 10 10"><path d="M2 0h6v3a3 3 0 0 1-6 0zM4 6h2v2h2v2H2V8h2z" fill="#FFC000"/></svg>Goal</div>
  </div>
  <h2 class="consumption-title"><span class="consumption-title__dot"></span>CONSUMPTION TODAY</h2>
  <div class="meter meter--danger"><div class="meter__track"><div class="meter__fill" style="width:64px"></div><div class="meter__knob" style="left:62px"></div></div>
    <div class="meter__scale"><span class="meter__name">Danger</span><span style="left:61px">01</span><span style="left:104px">02</span><span style="left:147px">03</span><span style="left:190px">04</span><span style="left:234px">05</span></div></div>
  <div class="meter meter--fatal"><div class="meter__track"><div class="meter__fill" style="width:150px"></div><div class="meter__knob" style="left:148px"></div></div>
    <div class="meter__scale"><span class="meter__name">Fatal</span><span style="left:61px">01</span><span style="left:104px">02</span><span style="left:147px">03</span><span style="left:190px">04</span><span style="left:234px">05</span></div></div>
  <div class="meter meter--catastrophe"><div class="meter__track"><div class="meter__fill" style="width:236px"></div><div class="meter__knob" style="left:233px"></div></div>
    <div class="meter__scale"><span class="meter__name">Catastrophe</span><span style="left:61px">01</span><span style="left:104px">02</span><span style="left:147px">03</span><span style="left:190px">04</span><span style="left:234px">05</span></div></div>
  <nav class="tab-bar">
    <span class="tab-bar__btn"><svg width="13" height="11" viewBox="0 0 13 11"><circle cx="3" cy="3" r="2" fill="#FFC000"/><circle cx="10" cy="3" r="2" fill="#FFC000"/><circle cx="6.5" cy="4" r="2.3" fill="#FFC000"/><path d="M1 11c0-4 11-4 11 0z" fill="#FFC000"/></svg></span>
    <span class="tab-bar__btn"><svg width="12" height="10" viewBox="0 0 12 10"><path d="M0 0h12v2H0zM0 4h12v2H0zM0 8h12v2H0z" fill="#FFC000"/></svg></span>
    <span class="tab-bar__start"><svg width="10" height="10" viewBox="0 0 10 10"><rect width="10" height="10" rx="2" fill="#0094D4"/><path d="M4 2h2v2h2v2H6v2H4V6H2V4h2z" fill="#fff"/></svg>Start</span>
    <span class="tab-bar__btn"><svg width="12" height="10" viewBox="0 0 12 10"><rect x="1" y="1" width="10" height="8" fill="none" stroke="#FFC000" stroke-width="1.6"/><path d="M6 1v8" stroke="#FFC000" stroke-width="1.6"/></svg></span>
    <span class="tab-bar__btn"><svg width="10" height="11" viewBox="0 0 10 11"><circle cx="5" cy="3" r="2.5" fill="#FFC000"/><path d="M0 11c0-5 10-5 10 0z" fill="#FFC000"/></svg></span>
  </nav>
</section>

<!-- Screen 2 : rehab monitor -->
<section class="screen screen--monitor">
  <header class="brand"><span class="brand__dot"></span><div class="brand__name"><div class="brand__title">GLIMWELL</div><div class="brand__tagline">DIABETES REVERSAL</div></div></header>
  <div class="header-rule"></div>
  <div class="section-bar"><span class="section-bar__icon"><svg width="20" height="18" viewBox="0 0 20 18"><circle cx="8" cy="8" r="6" fill="none" stroke="#FFC000" stroke-width="2"/><path d="M12.5 12.5l5 5" stroke="#FFC000" stroke-width="2.4"/><path d="M6 10V7M9 10V5" stroke="#FFC000" stroke-width="1.6"/></svg></span><span class="section-bar__label">REHAB MONITOR</span></div>
  <div class="chart-card chart-card--bars">
    <svg width="216" height="139" viewBox="0 0 216 139" font-family="Nunito, sans-serif" font-size="4" fill="#999">
      <g stroke="#ececec" stroke-width="0.8">
        <path d="M27 19v92M52 19v92M76 19v92M101 19v92M126 19v92M151 19v92M175 19v92M200 19v92"/>
      </g>
      <text x="16" y="28">JAN</text><text x="16" y="51">FEB</text><text x="16" y="73">MAR</text><text x="16" y="95">APR</text>
      <g>
        <rect x="27" y="24" width="26" height="4" rx="2" fill="#0094D4"/><rect x="27" y="31" width="14" height="4" rx="2" fill="#FFC000"/>
        <rect x="27" y="47" width="67" height="4" rx="2" fill="#0094D4"/><rect x="27" y="54" width="61" height="4" rx="2" fill="#FFC000"/>
        <rect x="27" y="69" width="77" height="4" rx="2" fill="#0094D4"/><rect x="27" y="76" width="108" height="4" rx="2" fill="#FFC000"/>
        <rect x="27" y="91" width="113" height="4" rx="2" fill="#0094D4"/><rect x="27" y="98" width="156" height="4" rx="2" fill="#FFC000"/>
      </g>
      <g text-anchor="middle"><text x="27" y="118">0</text><text x="52" y="118">100</text><text x="76" y="118">200</text><text x="101" y="118">300</text><text x="126" y="118">400</text><text x="151" y="118">500</text><text x="175" y="118">600</text><text x="200" y="118">700</text></g>
    </svg>
  </div>
  <div class="legend legend--bars"><span><i class="swatch-blue"></i>Fasting</span><span><i class="swatch-yellow"></i>Random</span></div>
  <div class="chart-card chart-card--lines">
    <svg width="216" height="105" viewBox="0 0 216 105" font-family="Nunito, sans-serif" font-size="3.6" fill="#999">
      <g stroke="#eeeeee" stroke-width="0.8"><path d="M24 16h168M24 26h168M24 36h168M24 45h168M24 55h168M24 64h168"/><path d="M60 14v66M95 14v66M129 14v66M164 14v66"/></g>
      <text x="14" y="27">Mon</text><text x="14" y="37">Tue</text><text x="14" y="46">Wed</text><text x="14" y="56">Thu</text><text x="14" y="75">Sat</text>
      <polyline points="24,16 60,45 95,49 129,40 164,45 190,45" fill="none" stroke="#7b7fe0" stroke-width="1"/>
      <polyline points="24,63 60,38 95,34 129,40 164,38 190,38" fill="none" stroke="#ef6f8e" stroke-width="1"/>
      <g fill="#fff" stroke="#7b7fe0" stroke-width="0.9"><circle cx="24" cy="16" r="2.4"/><circle cx="60" cy="45" r="2.4"/><circle cx="95" cy="49" r="2.4"/><circle cx="164" cy="45" r="2.4"/></g>
      <g fill="#fff" stroke="#ef6f8e" stroke-width="0.9"><circle cx="24" cy="63" r="2.4"/><circle cx="60" cy="38" r="2.4"/><circle cx="95" cy="34" r="2.4"/><circle cx="129" cy="40" r="2.4"/><circle cx="164" cy="38" r="2.4"/></g>
      <g text-anchor="middle" fill="#444"><text x="51" y="87">10 AM</text><text x="75" y="87">12 PM</text><text x="99" y="87">02 PM</text><text x="121" y="87">04 PM</text><text x="145" y="87">06 PM</text><text x="165" y="87">08 PM</text><text x="188" y="87">10 PM</text></g>
    </svg>
    <div class="legend legend--lines"><span><i class="swatch-blue"></i>Daily Walk</span><span><i class="swatch-yellow"></i>Daily Exercise</span></div>
  </div>
  <div class="stats">
    <div class="stat stat--weekly"><div class="stat__value">10</div><div class="stat__label">Sugar Bite Sent Weekly</div></div>
    <div class="stats__divider"></div>
    <div class="stat stat--avg"><div class="stat__value">07</div><div class="stat__label">Weekly Avg</div></div>
  </div>
  <nav class="tab-bar">
    <span class="tab-bar__btn"><svg width="13" height="11" viewBox="0 0 13 11"><circle cx="3" cy="3" r="2" fill="#FFC000"/><circle cx="10" cy="3" r="2" fill="#FFC000"/><circle cx="6.5" cy="4" r="2.3" fill="#FFC000"/><path d="M1 11c0-4 11-4 11 0z" fill="#FFC000"/></svg></span>
    <span class="tab-bar__btn"><svg width="12" height="10" viewBox="0 0 12 10"><path d="M0 0h12v2H0zM0 4h12v2H0zM0 8h12v2H0z" fill="#FFC000"/></svg></span>
    <span class="tab-bar__start"><svg width="10" height="10" viewBox="0 0 10 10"><rect width="10" height="10" rx="2" fill="#0094D4"/><path d="M4 2h2v2h2v2H6v2H4V6H2V4h2z" fill="#fff"/></svg>Start</span>
    <span class="tab-bar__btn"><svg width="12" height="10" viewBox="0 0 12 10"><rect x="1" y="1" width="10" height="8" fill="none" stroke="#FFC000" stroke-width="1.6"/><path d="M6 1v8" stroke="#FFC000" stroke-width="1.6"/></svg></span>
    <span class="tab-bar__btn"><svg width="10" height="11" viewBox="0 0 10 11"><circle cx="5" cy="3" r="2.5" fill="#FFC000"/><path d="M0 11c0-5 10-5 10 0z" fill="#FFC000"/></svg></span>
  </nav>
</section>

<!-- Screen 3 : daily feed -->
<section class="screen screen--daily-feed">
  <header class="brand"><span class="brand__dot"></span><div class="brand__name"><div class="brand__title">GLIMWELL</div><div class="brand__tagline">DIABETES REVERSAL</div></div></header>
  <div class="header-rule"></div>
  <div class="section-bar"><span class="section-bar__icon"><svg width="16" height="16" viewBox="0 0 16 16"><rect width="7" height="7" rx="1.5" fill="#FFC000"/><rect x="9" width="7" height="7" rx="1.5" fill="#FFC000"/><rect y="9" width="7" height="7" rx="1.5" fill="#FFC000"/><rect x="9" y="9" width="7" height="7" rx="1.5" fill="#FFC000"/></svg></span><span class="section-bar__label">DAILY FEED</span></div>
  <div class="field field--fasting"><div class="field__label">Fasting Sugar</div><div class="field__input">Type Here</div></div>
  <div class="field field--random"><div class="field__label">Random Sugar</div><div class="field__input">Type Here</div></div>
  <div class="field field--walk"><div class="field__label">Daily Walk Time / Distance</div><div class="field__input">Type Here</div></div>
  <nav class="tab-bar">
    <span class="tab-bar__btn"><svg width="13" height="11" viewBox="0 0 13 11"><circle cx="3" cy="3" r="2" fill="#FFC000"/><circle cx="10" cy="3" r="2" fill="#FFC000"/><circle cx="6.5" cy="4" r="2.3" fill="#FFC000"/><path d="M1 11c0-4 11-4 11 0z" fill="#FFC000"/></svg></span>
    <span class="tab-bar__btn"><svg width="12" height="10" viewBox="0 0 12 10"><path d="M0 0h12v2H0zM0 4h12v2H0zM0 8h12v2H0z" fill="#FFC000"/></svg></span>
    <span class="tab-bar__start"><svg width="10" height="10" viewBox="0 0 10 10"><rect width="10" height="10" rx="2" fill="#0094D4"/><path d="M4 2h2v2h2v2H6v2H4V6H2V4h2z" fill="#fff"/></svg>Start</span>
    <span class="tab-bar__btn"><svg width="12" height="10" viewBox="0 0 12 10"><rect x="1" y="1" width="10" height="8" fill="none" stroke="#FFC000" stroke-width="1.6"/><path d="M6 1v8" stroke="#FFC000" stroke-width="1.6"/></svg></span>
    <span class="tab-bar__btn"><svg width="10" height="11" viewBox="0 0 10 11"><circle cx="5" cy="3" r="2.5" fill="#FFC000"/><path d="M0 11c0-5 10-5 10 0z" fill="#FFC000"/></svg></span>
  </nav>
</section>

<!-- Screen 4 : rehab plan -->
<section class="screen screen--plan">
  <header class="brand"><span class="brand__dot"></span><div class="brand__name"><div class="brand__title">GLIMWELL</div><div class="brand__tagline">DIABETES REVERSAL</div></div></header>
  <div class="header-rule"></div>
  <div class="section-bar"><span class="section-bar__icon"><svg width="18" height="18" viewBox="0 0 18 18"><circle cx="4" cy="14" r="2.5" fill="none" stroke="#FFC000" stroke-width="1.6"/><circle cx="14" cy="4" r="2.5" fill="none" stroke="#FFC000" stroke-width="1.6"/><path d="M6.5 14H12a2.5 2.5 0 0 0 0-5H6a2.5 2.5 0 0 1 0-5h5.5" fill="none" stroke="#FFC000" stroke-width="1.6"/></svg></span><span class="section-bar__label">REHAB PLAN</span></div>
  <p class="plan-intro">See your plan to achieve no medicine diabetes control</p>
  <p class="plan-lead">Create your plan in just a few steps:</p>
  <div class="step step--1">Step 01</div><p class="step-text step-text--1">Choose desired date</p>
  <div class="step step--2">Step 02</div><p class="step-text step-text--2">Follow suggested diet</p>
  <div class="step step--3">Step 03</div><p class="step-text step-text--3">Enter your readings (Sugar, Frequency, Diet)</p>
  <nav class="tab-bar">
    <span class="tab-bar__btn"><svg width="13" height="11" viewBox="0 0 13 11"><circle cx="3" cy="3" r="2" fill="#FFC000"/><circle cx="10" cy="3" r="2" fill="#FFC000"/><circle cx="6.5" cy="4" r="2.3" fill="#FFC000"/><path d="M1 11c0-4 11-4 11 0z" fill="#FFC000"/></svg></span>
    <span class="tab-bar__btn"><svg width="12" height="10" viewBox="0 0 12 10"><path d="M0 0h12v2H0zM0 4h12v2H0zM0 8h12v2H0z" fill="#FFC000"/></svg></span>
    <span class="tab-bar__start"><svg width="10" height="10" viewBox="0 0 10 10"><rect width="10" height="10" rx="2" fill="#0094D4"/><path d="M4 2h2v2h2v2H6v2H4V6H2V4h2z" fill="#fff"/></svg>Start</span>
    <span class="tab-bar__btn"><svg width="12" height="10" viewBox="0 0 12 10"><rect x="1" y="1" width="10" height="8" fill="none" stroke="#FFC000" stroke-width="1.6"/><path d="M6 1v8" stroke="#FFC000" stroke-width="1.6"/></svg></span>
    <span class="tab-bar__btn"><svg width="10" height="11" viewBox="0 0 10 11"><circle cx="5" cy="3" r="2.5" fill="#FFC000"/><path d="M0 11c0-5 10-5 10 0z" fill="#FFC000"/></svg></span>
  </nav>
</section>

</div>
</body>
</html>
```